Website for Vornelix Capital, my new firm that raises money from investors to buy, build, own an...

Vornelix Capital needs a website! We are a new company with very experienced people, who invest in, own and build hotel properties, as well as apartments and other commercial real estate. We seek investors for our projects, and we provide safe, secure returns on their investment in our projects. Our new logo is designed to exhibit strength, class and security, and would like our website to continue on this theme. Our name, Vornelix, is a word-play on a Greek word “aristeia”, which means “excellence” and “a warriors finest moment of glory in war”. If you are in business, you realize that much of it is like war, with strategy and moves and opponents and competitors, and ever-changing economic conditions and threats that make business very much like war. We like to think that we are good at business (war), and so have named our company “Vornelix”, using the founders last name and the word “aristeia” combined. Another definition of "aristeia" is "performing at the peak of one's potential after a long struggle"...again, much like business in real life! The website design should exhibit financial security, smart moves, and positive growth towards a bright future.

Target Market(s)

The target market is smart and wealthy investors, with others such as brokers, cities and government agencies, lenders, sellers, partners, etc also looking at it.

Industry/Entity Type

Investment

Number of Pages Required

5+ page

Font styles to use
Sans Serif

Colors
fec214

Requirements
Must have
• Our website should have a landing page, a "about" or bio page, a projects page and a contact us page. Our new logo uses the colors black and gold, so this should be factored in to our site. The site should be simple, yet impactful and impressive. I have actually two logos, which can be mixed and interchanged in a complimentary way, each with their own unique look.
Nice to have
• I have uploaded a couple screenshots of a website i like, and the simplicity I mention.
Should not have
• The site should not be flashy or complicated or complex or "busy"

```html
<!DOCTYPE html>
<html lang="en">
<head>
<meta charset="utf-8">
<title>Vornelix Capital</title>
<link rel="stylesheet" href="https://fonts.googleapis.com/css2?family=Poppins:wght@400;500;600&family=Open+Sans:wght@400;600&display=swap">
<style>
:root{
  --gold:#fec214;
  --gold-deep:#c7901a;
  --ink:#111111;
  --text:#333333;
  --muted:#555555;
  --line:#bfbfbf;
  --soft:#f3f3f3;
  --footer:#0d0d0d;
}
*{margin:0;padding:0;box-sizing:border-box}
html,body{width:1200px;height:3448px;overflow:hidden}
body{font-family:"Open Sans",Arial,sans-serif;color:var(--text);background:#fff;position:relative}
.abs{position:absolute}
.btn{position:absolute;background:var(--gold);color:#fff;font-family:"Poppins",Arial,sans-serif;font-weight:500;text-transform:uppercase;border-radius:30px;display:flex;align-items:center;justify-content:center;letter-spacing:.5px}
.gold{color:var(--gold-deep)}

/* hero */
.hero{left:0;top:0;width:1200px;height:685px;background:linear-gradient(180deg,#dfe8f0 0%,#b9cad8 45%,#5d7e97 100%)}
.brand{left:92px;top:60px;display:flex;align-items:center;gap:12px;font-family:"Poppins",Arial,sans-serif;font-weight:600;font-size:30px;color:var(--ink);letter-spacing:1px}
.brand i{width:22px;height:22px;background:var(--gold-deep);display:block}
.nav{left:498px;top:56px;display:flex;gap:36px;font-size:20px;color:var(--ink)}
.nav .active{color:var(--gold-deep)}
.phone{left:952px;top:50px;display:flex;align-items:center;gap:12px;font-size:23px;color:var(--ink)}
.hero-title{left:0;top:248px;width:1200px;text-align:center;font-family:"Poppins",Arial,sans-serif;font-weight:500;font-size:80px;line-height:100px;color:var(--gold);letter-spacing:1px}
.hero-sub{left:0;top:360px;width:1200px;text-align:center;font-family:"Poppins",Arial,sans-serif;font-weight:500;font-size:31px;line-height:40px;color:var(--ink)}
.arrow{width:24px;height:24px;border-radius:50%;background:rgba(60,60,60,.75);display:flex;align-items:center;justify-content:center}

/* about */
.section-title{position:absolute;left:0;width:1200px;text-align:center;font-family:"Poppins",Arial,sans-serif;font-weight:500;font-size:48px;color:var(--ink)}
.about-text{left:128px;top:876px;width:944px;text-align:center;font-size:19px;line-height:31px;color:var(--text)}

/* services */
.services-left{left:0;top:1168px;width:759px;height:621px;background:linear-gradient(90deg,#f1f1f1,#fafafa)}
.services-right{left:759px;top:1168px;width:441px;height:621px;background:linear-gradient(135deg,#d4a12a,#b47f12)}
.services-title{left:87px;top:1264px;font-family:"Poppins",Arial,sans-serif;font-weight:500;font-size:44px;line-height:54px;color:var(--ink)}
.services-text{left:87px;top:1382px;width:336px;font-size:13px;line-height:22px;color:var(--text)}
.services-text p+p{margin-top:8px}
.services-card{left:471px;top:1246px;width:651px;height:474px;background:#fff;box-shadow:0 2px 14px rgba(0,0,0,.12)}
.service{position:absolute;width:280px;text-align:center}
.service .ico{width:70px;height:70px;margin:0 auto;border-radius:50%;background:var(--gold);border:5px solid #ffe07a;display:flex;align-items:center;justify-content:center}
.service h3{margin-top:18px;font-family:"Poppins",Arial,sans-serif;font-size:14px;font-weight:600;color:var(--ink)}
.service p{margin-top:6px;font-size:13px;line-height:19px;color:var(--muted)}

/* projects */
.project{position:absolute;top:2032px;width:489px;height:382px;background:#fff;box-shadow:0 2px 10px rgba(0,0,0,.16)}
.project .photo{height:221px}
.project h3{margin:25px 0 0 30px;font-family:"Poppins",Arial,sans-serif;font-weight:400;font-size:21px;color:var(--ink)}
.project p{margin:14px 26px 0 30px;font-size:12px;line-height:20px;color:var(--muted)}
.project a{display:inline-block;margin:10px 0 0 30px;font-size:11px;color:var(--gold-deep);text-decoration:none;border-bottom:1px solid var(--gold-deep);padding-bottom:2px;text-transform:uppercase}

/* touch */
.touch{left:0;top:2529px;width:1200px;height:281px;background:linear-gradient(135deg,#c9941c,#e0ab2e 50%,#b9841a)}
.touch h2{position:absolute;left:0;top:60px;width:1200px;text-align:center;font-family:"Poppins",Arial,sans-serif;font-weight:500;font-size:39px;color:#fff}
.socials{position:absolute;left:288px;top:142px;display:flex;gap:28px}
.socials span{width:64px;height:64px;border:2px solid #fff;border-radius:50%;display:block}

/* contact */
.contact-bg{left:0;top:2810px;width:1200px;height:514px;background:radial-gradient(ellipse at 30% 40%,#eef0f2 0%,#fff 65%)}
.contact-head{position:absolute;top:2930px;font-family:"Poppins",Arial,sans-serif;font-weight:500;font-size:19px;color:var(--ink);text-transform:uppercase}
.contact-head span{color:var(--gold-deep)}
.info{position:absolute;left:124px;display:flex;gap:38px}
.info .txt{font-size:14px;line-height:20px;color:var(--text)}
.info .txt b{font-weight:600;display:block;margin-bottom:2px;color:var(--ink)}
.field{position:absolute;left:593px;width:483px;height:41px;border:1px solid var(--line);background:#fff;font-size:14px;color:#444;padding:10px 14px}
.submit{left:966px;top:3243px;width:110px;height:28px;font-size:14px}

.footer{left:0;top:3324px;width:1200px;height:124px;background:var(--footer)}
.footer p{position:absolute;left:0;top:54px;width:1200px;text-align:center;font-size:13px;color:#aaa}
</style>
</head>
<body>

<header class="abs hero" role="img" aria-label="Photo of stacked coins before a city skyline with a rising growth line"></header>
<div class="abs brand"><i></i>VORNELIX</div>
<nav class="abs nav"><span class="active">Home</span><span>About</span><span>Projects</span><span>Contact us</span></nav>
<div class="abs phone">
  <svg width="30" height="30" viewBox="0 0 30 30"><circle cx="15" cy="15" r="13" fill="none" stroke="#c7901a" stroke-width="2"/><path d="M10 8l3 0 1 4-2 1.5c1 2 2.5 3.5 4.5 4.5L18 16l4 1v3c0 1-1 2-2 2C14 21.5 8.5 16 8 10c0-1 1-2 2-2z" fill="#c7901a"/></svg>
  5550192847
</div>
<div class="abs arrow" style="left:58px;top:351px"><svg width="10" height="10" viewBox="0 0 10 10"><path d="M6.5 1.5L3 5l3.5 3.5" stroke="#fff" stroke-width="1.8" fill="none"/></svg></div>
<div class="abs arrow" style="left:1115px;top:351px"><svg width="10" height="10" viewBox="0 0 10 10"><path d="M3.5 1.5L7 5 3.5 8.5" stroke="#fff" stroke-width="1.8" fill="none"/></svg></div>
<h1 class="abs hero-title">VORNELIX CAPITAL</h1>
<p class="abs hero-sub">Neque porro quisquam qui dolorem ipsum dolor amet</p>
<a class="btn" style="left:501px;top:439px;width:198px;height:52px;font-size:21px">View More</a>

<section>
  <h2 class="section-title" style="top:798px">About <span class="gold">Vornelix Capital</span></h2>
  <p class="abs about-text">It is a long established fact that a reader will be distracted by the readable content of a page when looking at its layout. The point of using Lorem Ipsum is that it has a more-or-less normal distribution of letters, as opposed to using 'Content here, content here', making it look like readable English. Many desktop publishing packages and web page editors now use Lorem Ipsum as their default model text,</p>
  <a class="btn" style="left:516px;top:1028px;width:168px;height:44px;font-size:18px">Read More</a>
</section>

<section>
  <div class="abs services-left" role="img" aria-label="Faint circuit-line and dotted wave background"></div>
  <div class="abs services-right" role="img" aria-label="Gold-tinted photo of a desk with a laptop"></div>
  <h2 class="abs services-title"><span class="gold">Our</span><br>Services</h2>
  <div class="abs services-text">
    <p>It is a long established fact that a reader will be distracted by the readable content of a page when looking at its layout. The point of using Lorem Ipsum is that it has a more-or-less normal distribution of letters, as opposed to using 'Content here, content here'.</p>
    <p>Making it look like readable English. Many desktop publishing packages and web page editors now use Lorem Ipsum as their default model text, and a search for 'lorem ipsum' will uncover many web sites still in their infancy various versions have evolved.</p>
  </div>
  <a class="btn" style="left:87px;top:1645px;width:128px;height:36px;font-size:14px">Read More</a>
  <div class="abs services-card">
    <div class="service" style="left:48px;top:50px">
      <div class="ico"><svg width="34" height="28" viewBox="0 0 34 28"><rect x="2" y="2" width="30" height="19" rx="2" fill="none" stroke="#fff" stroke-width="2"/><path d="M7 16l6-6 5 4 8-7" stroke="#fff" stroke-width="2" fill="none"/><path d="M12 26h10" stroke="#fff" stroke-width="2"/></svg></div>
      <h3>NEQUE PORRO QUISQUAM</h3>
      <p>Lorem ipsum dolor sit amet,<br>consectetur adipiscing elit, sed do<br>e.iusmod tempor incididunt</p>
    </div>
    <div class="service" style="left:325px;top:50px">
      <div class="ico"><svg width="32" height="32" viewBox="0 0 32 32"><circle cx="14" cy="14" r="10" fill="none" stroke="#fff" stroke-width="2"/><path d="M9 14l4 4 7-8M21 21l8 8" stroke="#fff" stroke-width="2.4" fill="none"/></svg></div>
      <h3>DOLOREM IPSUM QUIA</h3>
      <p>Lorem ipsum dolor sit amet,<br>consectetur adipiscing elit, sed do<br>e.iusmod tempor incididunt</p>
    </div>
    <div class="service" style="left:48px;top:260px">
      <div class="ico"><svg width="30" height="32" viewBox="0 0 30 32"><circle cx="15" cy="9" r="6" fill="none" stroke="#fff" stroke-width="2"/><path d="M3 30c0-7 5-12 12-12s12 5 12 12z" fill="none" stroke="#fff" stroke-width="2"/></svg></div>
      <h3>IPSUM QUIA DOLOR</h3>
      <p>Lorem ipsum dolor sit amet,<br>consectetur adipiscing elit, sed do<br>e.iusmod tempor incididunt</p>
    </div>
    <div class="service" style="left:325px;top:260px">
      <div class="ico"><svg width="26" height="32" viewBox="0 0 26 32"><rect x="2" y="2" width="22" height="28" rx="2" fill="none" stroke="#fff" stroke-width="2"/><path d="M7 10h12M7 15h12M7 20h12M7 25h8" stroke="#fff" stroke-width="2"/></svg></div>
      <h3>PORRO QUISQUAM EST</h3>
      <p>Lorem ipsum dolor sit amet,<br>consectetur adipiscing elit, sed do<br>e.iusmod tempor incididunt</p>
    </div>
  </div>
</section>

<section>
  <h2 class="section-title" style="top:1922px">Our <span class="gold">Projects</span></h2>
  <article class="project" style="left:92px">
    <div class="photo" role="img" aria-label="Photo of a modern glass apartment block under a blue sky" style="background:linear-gradient(180deg,#4d7fd0,#9fb8d8 60%,#4b5563)"></div>
    <h3>Neque porro quisquam</h3>
    <p>The point of using Lorem Ipsum is that it has a more-or-less normal distribution of letters, as opposed to using 'Content here, content here',</p>
    <a>Read More</a>
  </article>
  <article class="project" style="left:616px">
    <div class="photo" role="img" aria-label="Photo of a white colonial hotel building with palm trees" style="background:linear-gradient(180deg,#a9b7c4,#d9dcd6 45%,#4f6b3c)"></div>
    <h3>Dolorem ipsum quia dolor</h3>
    <p>The point of using Lorem Ipsum is that it has a more-or-less normal distribution of letters, as opposed to using 'Content here, content here',</p>
    <a>Read More</a>
  </article>
</section>

<section class="abs touch" role="img" aria-label="Gold-tinted photo of hands on a laptop keyboard">
  <h2>Get in Touch</h2>
  <div class="socials"><span></span><span></span><span></span><span></span><span></span><span></span><span></span></div>
</section>

<section>
  <div class="abs contact-bg" role="img" aria-label="Faint dotted particle wave background"></div>
  <h3 class="contact-head" style="left:124px">Contact <span>Us</span></h3>
  <div class="info" style="top:2990px">
    <svg width="46" height="34" viewBox="0 0 46 34"><rect x="2" y="2" width="42" height="30" fill="none" stroke="#c7901a" stroke-width="2"/><path d="M2 2l21 17L44 2" stroke="#c7901a" stroke-width="2" fill="none"/></svg>
    <div class="txt"><b>Email</b>hello@vornelixmail.net</div>
  </div>
  <div class="info" style="top:3075px">
    <svg width="46" height="50" viewBox="0 0 46 50"><rect x="10" y="2" width="26" height="46" rx="3" fill="none" stroke="#c7901a" stroke-width="2"/><path d="M10 10h26M10 38h26" stroke="#c7901a" stroke-width="2"/></svg>
    <div class="txt"><b>Call Us !</b>+555 210 4417<br>+555 210 4417</div>
  </div>
  <div class="info" style="top:3180px">
    <svg width="46" height="50" viewBox="0 0 46 50"><path d="M23 46C10 30 8 24 8 18a15 15 0 0130 0c0 6-2 12-15 28z" fill="none" stroke="#c7901a" stroke-width="2"/><circle cx="23" cy="18" r="5" fill="none" stroke="#c7901a" stroke-width="2"/></svg>
    <div class="txt"><b>Address</b>48, Harbor Lane, Westfield,<br>Northland 204518</div>
  </div>

  <h3 class="contact-head" style="left:589px">Contact <span>Form</span></h3>
  <div class="field" style="top:2991px">Name</div>
  <div class="field" style="top:3041px">Email</div>
  <div class="field" style="top:3092px">Phone</div>
  <div class="field" style="top:3143px;height:91px">Message</div>
  <a class="btn submit">Submit</a>
</section>

<footer class="abs footer">
  <p>© 2018 Company Name &nbsp;All right reserved</p>
</footer>

</body>
</html>
```